Doors for Chiropractic Office

In my chiropractic office I have 6 treatment rooms and 2 massage rooms. The entire office is going through a remodel. The overall color scheme is very earth tones but in order to add some color, the 6 doors to the treatment rooms will all be a separate color (Red, Blue, Yellow, Green etc)
I need to number each room 1,2,3,4,5,6 and the 2 massage rooms. I had the idea of putting a giant number on each door, so I am looking for some graphic ideas for that project.
The rooms are located with 4 on each side of a long hallway with the 2 massage rooms at the end.
The purpose of numbering each door is to direct the patients where to go.
I have uploaded pictures of the hall way. Pardon the dust since we are under construction but hopefully it gives you an idea of the layout. The door colors will change as stated above.

Requirements
Nice to have
• I would like to see someone come up with a design where each number for the doors are created out of vertebrae's.

```html
<!DOCTYPE html>
<html lang="en">
<head>
<meta charset="utf-8">
<title>Door Signs – Treatment and Massage Rooms</title>
<link rel="stylesheet" href="https://fonts.googleapis.com/css2?family=Anton&display=swap">
<style>
  :root {
    --bg: #ececec;
    --white: #ffffff;
    --red: #d63238;      --red-dark: #b52a30;
    --blue: #35abe0;     --blue-dark: #1f93cc;
    --yellow: #fcd62a;   --yellow-dark: #e8bb22;
    --green: #13a050;    --green-dark: #0d8540;
    --brown: #7b4631;    --brown-dark: #633624;
    --grey: #6a6a6c;     --grey-dark: #555557;
    --olive: #8a9645;    --olive-dark: #717d35;
    --ochre: #9c7a3e;    --ochre-dark: #7d602c;
  }
  html, body {
    margin: 0; padding: 0;
    width: 1200px; height: 429px;
    overflow: hidden;
    background: var(--bg);
  }
  .signage {
    position: relative;
    width: 1200px; height: 429px;
    font-family: "Anton", "Oswald", sans-serif;
  }
  .door-sign {
    position: absolute;
    top: 99px;
    width: 115px; height: 230px;
    background: var(--c);
    box-shadow: 0 2px 4px rgba(0,0,0,0.25);
  }
  .door-sign--red    { --c: var(--red);    --d: var(--red-dark); }
  .door-sign--blue   { --c: var(--blue);   --d: var(--blue-dark); }
  .door-sign--yellow { --c: var(--yellow); --d: var(--yellow-dark); }
  .door-sign--green  { --c: var(--green);  --d: var(--green-dark); }
  .door-sign--brown  { --c: var(--brown);  --d: var(--brown-dark); }
  .door-sign--grey   { --c: var(--grey);   --d: var(--grey-dark); }
  .door-sign--olive  { --c: var(--olive);  --d: var(--olive-dark); }
  .door-sign--ochre  { --c: var(--ochre);  --d: var(--ochre-dark); }

  .number-frame {
    position: absolute;
    left: 26px; top: 20px;
    width: 63px; height: 42px;
    border: 1px solid rgba(255,255,255,0.85);
    box-sizing: border-box;
  }
  .door-sign--massage .number-frame { top: 26px; height: 42px; }

  .number-card {
    position: absolute;
    left: 31px; top: 25px;
    width: 53px; height: 56px;
    background: var(--white);
    overflow: hidden;
    text-align: center;
  }
  .door-sign--massage .number-card { top: 24px; height: 64px; }

  .number-card__band {
    position: absolute; left: 0; top: 0;
    width: 53px; height: 30px;
    display: block;
  }
  .number-card__band path { fill: var(--d); }

  .number-card__label {
    position: relative;
    display: block;
    color: var(--white);
    font-size: 11px;
    line-height: 11px;
    padding-top: 3px;
    letter-spacing: 0.2px;
  }
  .door-sign--massage .number-card__label {
    font-size: 11px;
    line-height: 11.5px;
    padding-top: 2px;
  }
  .number-card__digits {
    position: absolute;
    left: 0; right: 0; bottom: 2px;
    color: var(--c);
    font-size: 32px;
    line-height: 34px;
    letter-spacing: -0.5px;
  }

  .practice-name {
    position: absolute;
    right: 10px; bottom: 12px;
    display: flex; align-items: center; gap: 2px;
    color: var(--white);
    font-size: 5px;
    letter-spacing: 0.3px;
    white-space: nowrap;
  }
  .practice-name__dot {
    width: 7px; height: 7px;
    border: 1px solid var(--white);
    border-radius: 50%;
    box-sizing: border-box;
  }
</style>
</head>
<body>
<main class="signage">

  <section class="door-sign door-sign--red" style="left:77px">
    <div class="number-frame"></div>
    <div class="number-card">
      <svg class="number-card__band" viewBox="0 0 53 30" preserveAspectRatio="none"><path d="M0 0H53V15Q26.5 23 0 15Z"/></svg>
      <span class="number-card__label">ROOM</span>
      <span class="number-card__digits">01</span>
    </div>
    <div class="practice-name"><span class="practice-name__dot"></span>MEADOW SPINE CARE</div>
  </section>

  <section class="door-sign door-sign--blue" style="left:205px">
    <div class="number-frame"></div>
    <div class="number-card">
      <svg class="number-card__band" viewBox="0 0 53 30" preserveAspectRatio="none"><path d="M0 0H53V15Q26.5 23 0 15Z"/></svg>
      <span class="number-card__label">ROOM</span>
      <span class="number-card__digits">02</span>
    </div>
    <div class="practice-name"><span class="practice-name__dot"></span>MEADOW SPINE CARE</div>
  </section>

  <section class="door-sign door-sign--yellow" style="left:334px">
    <div class="number-frame"></div>
    <div class="number-card">
      <svg class="number-card__band" viewBox="0 0 53 30" preserveAspectRatio="none"><path d="M0 0H53V15Q26.5 23 0 15Z"/></svg>
      <span class="number-card__label">ROOM</span>
      <span class="number-card__digits">03</span>
    </div>
    <div class="practice-name"><span class="practice-name__dot"></span>MEADOW SPINE CARE</div>
  </section>

  <section class="door-sign door-sign--green" style="left:463px">
    <div class="number-frame"></div>
    <div class="number-card">
      <svg class="number-card__band" viewBox="0 0 53 30" preserveAspectRatio="none"><path d="M0 0H53V15Q26.5 23 0 15Z"/></svg>
      <span class="number-card__label">ROOM</span>
      <span class="number-card__digits">04</span>
    </div>
    <div class="practice-name"><span class="practice-name__dot"></span>MEADOW SPINE CARE</div>
  </section>

  <section class="door-sign door-sign--brown" style="left:591px">
    <div class="number-frame"></div>
    <div class="number-card">
      <svg class="number-card__band" viewBox="0 0 53 30" preserveAspectRatio="none"><path d="M0 0H53V15Q26.5 23 0 15Z"/></svg>
      <span class="number-card__label">ROOM</span>
      <span class="number-card__digits">05</span>
    </div>
    <div class="practice-name"><span class="practice-name__dot"></span>MEADOW SPINE CARE</div>
  </section>

  <section class="door-sign door-sign--grey" style="left:719px">
    <div class="number-frame"></div>
    <div class="number-card">
      <svg class="number-card__band" viewBox="0 0 53 30" preserveAspectRatio="none"><path d="M0 0H53V15Q26.5 23 0 15Z"/></svg>
      <span class="number-card__label">ROOM</span>
      <span class="number-card__digits">06</span>
    </div>
    <div class="practice-name"><span class="practice-name__dot"></span>MEADOW SPINE CARE</div>
  </section>

  <section class="door-sign door-sign--olive door-sign--massage" style="left:882px">
    <div class="number-frame"></div>
    <div class="number-card">
      <svg class="number-card__band" viewBox="0 0 53 30" preserveAspectRatio="none"><path d="M0 0H53V25Q26.5 31 0 25Z"/></svg>
      <span class="number-card__label">MASSAGE<br>ROOM</span>
      <span class="number-card__digits">01</span>
    </div>
    <div class="practice-name"><span class="practice-name__dot"></span>MEADOW SPINE CARE</div>
  </section>

  <section class="door-sign door-sign--ochre door-sign--massage" style="left:1007px">
    <div class="number-frame"></div>
    <div class="number-card">
      <svg class="number-card__band" viewBox="0 0 53 30" preserveAspectRatio="none"><path d="M0 0H53V25Q26.5 31 0 25Z"/></svg>
      <span class="number-card__label">MASSAGE<br>ROOM</span>
      <span class="number-card__digits">02</span>
    </div>
    <div class="practice-name"><span class="practice-name__dot"></span>MEADOW SPINE CARE</div>
  </section>

</main>
</body>
</html>
```